Maple Gable Business Card

Colors can be blue, grey and white as you see in the attached logo. Needs to have a spot for name, title, phone, email, address, and website. There also needs to be a spot for an agent's picture.

Contact Information for Business Card

See project description.

Colors

Designer to choose colors to be used in the design.

```html
<!DOCTYPE html>
<html lang="en">
<head>
<meta charset="utf-8">
<title>Maple Gable Business Card</title>
<link rel="stylesheet" href="https://fonts.googleapis.com/css2?family=Roboto:wght@300;400;500&display=swap">
<style>
  :root {
    --backdrop: #9b9b9b;
    --brand-blue: #2777b6;
    --ink-dark: #3b3b3b;
    --ink-soft: #555555;
    --rule: #3f3f3f;
    --card-white: #ffffff;
    --photo-light: #dfe7ef;
    --photo-dark: #b9c8d6;
  }
  * { box-sizing: border-box; margin: 0; padding: 0; }
  html, body {
    width: 1200px; height: 900px; overflow: hidden;
    background: var(--backdrop);
    font-family: "Roboto", Arial, sans-serif;
  }
  .stage { position: relative; width: 1200px; height: 900px; }
  .card {
    position: absolute; top: 214px;
    width: 270px; height: 474px;
    border-radius: 18px;
  }
  .card--front { left: 288px; background: var(--brand-blue); }
  .card--back { left: 641px; background: var(--card-white); }

  .wordmark {
    position: absolute; left: 0; right: 0;
    display: flex; align-items: center; justify-content: center; gap: 8px;
    font-weight: 500; font-size: 24px; line-height: 28px; letter-spacing: 0.5px;
  }
  .wordmark__square { width: 14px; height: 14px; }
  .card--front .wordmark { top: 222px; color: var(--card-white); }
  .card--front .wordmark__square { background: var(--card-white); }
  .card--back .wordmark { top: 96px; color: var(--brand-blue); }
  .card--back .wordmark__square { background: var(--brand-blue); }

  .agent-photo {
    position: absolute; top: 166px; left: 104px;
    width: 62px; height: 62px; border-radius: 50%;
    background: linear-gradient(160deg, var(--photo-light), var(--photo-dark));
    border: 2px solid var(--brand-blue);
  }

  .agent { position: absolute; left: 0; right: 0; text-align: center; }
  .agent__name { top: 246px; font-weight: 500; font-size: 20px; line-height: 22px; color: var(--brand-blue); }
  .agent__title { top: 268px; font-weight: 400; font-size: 15px; line-height: 18px; color: var(--ink-dark); }

  .divider { position: absolute; left: 58px; width: 155px; height: 1px; background: var(--rule); }
  .divider--icons { top: 301px; }
  .divider--plain { top: 380px; }

  .icon-row {
    position: absolute; top: 293px; left: 0; right: 0;
    display: flex; justify-content: center; gap: 3px;
  }
  .icon-row__item {
    width: 16px; height: 16px; border-radius: 50%;
    background: var(--brand-blue);
    box-shadow: 0 0 0 2px var(--card-white);
    display: flex; align-items: center; justify-content: center;
  }

  .contact {
    position: absolute; left: 0; right: 0; top: 318px;
    text-align: center; font-weight: 300; font-size: 14px; line-height: 17px;
    color: var(--ink-soft);
  }
  .contact__highlight { color: var(--brand-blue); }
  .address {
    position: absolute; left: 0; right: 0; top: 390px;
    text-align: center; font-weight: 300; font-size: 14px; line-height: 17px;
    color: var(--ink-soft);
  }
</style>
</head>
<body>
<main class="stage">
  <section class="card card--front" aria-label="Card front">
    <div class="wordmark"><span class="wordmark__square"></span>Maple Gable</div>
  </section>

  <section class="card card--back" aria-label="Card back">
    <div class="wordmark"><span class="wordmark__square"></span>Maple Gable</div>

    <div class="agent-photo" role="img" aria-label="Agent portrait photo"></div>

    <p class="agent agent__name">Daniel Hartley</p>
    <p class="agent agent__title">Manager</p>

    <div class="divider divider--icons"></div>
    <div class="icon-row">
      <span class="icon-row__item" aria-label="Phone">
        <svg width="10" height="10" viewBox="0 0 10 10"><path d="M2 1.5 L3.5 1.5 L4 3.5 L3 4.2 Q4 6.2 5.8 7 L6.5 6 L8.5 6.5 L8.5 8 Q5 8.8 2.6 6.5 Q1.2 4.8 2 1.5Z" fill="#fff"/></svg>
      </span>
      <span class="icon-row__item" aria-label="Email">
        <svg width="10" height="10" viewBox="0 0 10 10"><rect x="1" y="2.5" width="8" height="5.5" fill="none" stroke="#fff" stroke-width="1"/><path d="M1 2.5 L5 5.6 L9 2.5" fill="none" stroke="#fff" stroke-width="1"/></svg>
      </span>
      <span class="icon-row__item" aria-label="Website">
        <svg width="10" height="10" viewBox="0 0 10 10"><circle cx="5" cy="5" r="3.8" fill="none" stroke="#fff" stroke-width="1"/><ellipse cx="5" cy="5" rx="1.6" ry="3.8" fill="none" stroke="#fff" stroke-width="0.8"/><line x1="1.2" y1="5" x2="8.8" y2="5" stroke="#fff" stroke-width="0.8"/></svg>
      </span>
    </div>

    <p class="contact">
      123-456-2100<br>
      youremail@mailbox.com<br>
      www.<span class="contact__highlight">yourwebsite</span>.com
    </p>

    <div class="divider divider--plain"></div>

    <p class="address">Your address, city<br>state, ZIP 0000</p>
  </section>
</main>
</body>
</html>
```